Interior Design & Furniture E commerce Website Design

I need a cutting edge website design, this is for Interior Design Services as well as eCommerce for furniture and home decor www.lorivexstudio.com
Here is a sample of the concept behind the site.
I am a furniture & Interior Designer, want to create a life style brand.
Will offer Interior Design Services : Commercial & Residential (this portion will be a catalog or portfolio type)
The eCommerce side will sell, Furniture, Lighting, Decor, Gifts, Textiles, will also be offering trade so that could be at bottom of site. I also like the concept of concierge as where all the info falls under: shipping, etc..

*Please make sure to make the eCommerce prominent.

Gathering more feedback

Hello Designers, I also would like to possibly update my logo, the current one I like but don't Love.

Target Market(s)

High end customers with disposable income, who also appreciate quality and unique furniture & design

Number of Pages Required

5+ page

Colors
0255a3
f37122

Requirements
Must have
• Room Planer: I will be using this tool http://qtstudio.velbarnix.com/room-planner.inc
• Live Chat
• Will be offering 3d renderings for spaces as well as Virtual Reality
• The image I loaded that looks like copper, I would like to have that as a color on the site with the texture: so the colors are Blue and copper. Would like the site to be user friendly and interactive
• http://qtstudio.velbarnix.com/ (this is the current site in development, so we will be offering Design your own, Trends, inspiration, etc...
• I have included a headshot to use for now about me. or about us.
• I also included several actual project installation (residential and commercial) as well as a variety of my furniture items
• I have Included an old Bio and some articles I would like to show case in a Press Area
• I would also like to include a section for Events (Giving back )I do a lot of charity events 1-2 a year and would like to showcase that as well
• *Please make the store (ecommerce prominent )

```html
<!DOCTYPE html>
<html lang="en">
<head>
<meta charset="utf-8">
<title>Lori Vex Studio — Interior Design &amp; Furniture</title>
<link href="https://fonts.googleapis.com/css2?family=Open+Sans:wght@400;600;700;800&display=swap" rel="stylesheet">
<style>
:root{
  --blue:#0255a3;
  --blue-glass:rgba(2,85,163,.88);
  --orange:#f37122;
  --copper:#b86b3c;
  --copper-light:#d9955f;
  --ink:#2a2a2a;
  --text:#555;
  --muted:#8a8a8a;
  --line:#e3e3e3;
  --soft:#f2f2f2;
  --footer:#262626;
  --white:#fff;
}
*{box-sizing:border-box;margin:0;padding:0}
html,body{width:1200px;height:4876px;overflow:hidden}
body{font-family:"Open Sans",Arial,sans-serif;color:var(--text);background:var(--white);font-size:13px;line-height:1.6}
.btn{display:inline-block;background:var(--orange);color:var(--white);font-weight:700;font-size:12px;letter-spacing:.5px;text-transform:uppercase;padding:9px 20px;border-radius:2px}
.btn-sm{font-size:10px;padding:5px 12px}
.section-title{font-size:30px;font-weight:800;color:var(--ink);text-align:center;text-transform:uppercase;letter-spacing:.5px}
.photo{display:block}

/* header */
.site-header{height:152px;position:relative;border-bottom:1px solid var(--line)}
.brand{position:absolute;left:140px;top:26px;width:170px;height:96px;display:flex;align-items:center;justify-content:center;gap:10px}
.brand-square{width:14px;height:14px;background:var(--copper)}
.brand-name{font-size:20px;font-weight:700;color:var(--copper);letter-spacing:2px;text-transform:uppercase;line-height:1.2;width:120px}
.search{position:absolute;left:380px;top:38px;display:flex;height:32px;border:1px solid #cfcfcf}
.search-cat{width:92px;font-size:11px;padding:7px 10px;border-right:1px solid #cfcfcf;color:var(--ink)}
.search-input{width:228px;font-size:11px;padding:7px 10px;color:var(--muted)}
.search-go{width:40px;background:var(--orange);display:flex;align-items:center;justify-content:center}
.call{position:absolute;left:768px;top:34px;display:flex;gap:10px;align-items:center}
.call-icon{width:34px;height:34px;border-radius:50%;background:var(--orange);display:flex;align-items:center;justify-content:center}
.call small{display:block;font-size:10px;color:var(--muted);font-weight:600;line-height:1.2}
.call strong{font-size:17px;color:var(--orange);font-weight:800;line-height:1.2}
.cart{position:absolute;left:1000px;top:42px;font-size:11px;font-weight:700;color:var(--ink);display:flex;gap:6px;align-items:center}
.main-nav{position:absolute;left:370px;top:100px;display:flex;gap:26px}
.main-nav a{font-size:11px;color:var(--ink);font-weight:600;text-decoration:none;display:flex;flex-direction:column;align-items:center;gap:3px}

/* hero */
.hero{height:548px;position:relative;background:linear-gradient(180deg,#5b4a3a 0%,#8a6a4f 45%,#6a3a2c 75%,#3b2b22 100%);color:var(--white);text-align:center}
.hero h1{position:absolute;top:84px;left:0;right:0;font-size:44px;font-weight:800;line-height:1.12;text-transform:uppercase;letter-spacing:1px}
.hero .btn{position:absolute;top:174px;left:538px;font-size:14px;padding:10px 26px}
.dots{position:absolute;bottom:44px;left:0;right:0;display:flex;justify-content:center;gap:10px}
.dots span{width:10px;height:10px;border-radius:50%;background:rgba(255,255,255,.55)}
.dots span.on{background:var(--white)}

/* categories + features */
.collections{height:460px;position:relative}
.cat-grid{position:absolute;top:32px;left:132px;display:flex;gap:16px}
.cat-card{width:304px;height:248px;position:relative}
.cat-card:nth-child(1) .photo{background:linear-gradient(160deg,#4a2a20,#a0523a 55%,#2e1b15)}
.cat-card:nth-child(2) .photo{background:linear-gradient(160deg,#3a2e26,#8c6f55 55%,#2a211b)}
.cat-card:nth-child(3) .photo{background:linear-gradient(160deg,#6f6f78,#b7b2ad 55%,#5a5555)}
.cat-card .photo{width:100%;height:100%}
.cat-label{position:absolute;left:14px;right:14px;bottom:14px;display:flex;justify-content:space-between;align-items:center}
.cat-label b{color:var(--white);font-size:19px;font-weight:700;text-transform:uppercase;letter-spacing:.5px}
.features{position:absolute;top:308px;left:132px;display:flex;gap:16px}
.feature{width:304px;height:80px;border:4px solid var(--copper);display:flex;align-items:center;gap:14px;padding:0 18px}
.feature h3{font-size:14px;color:var(--ink);font-weight:700;line-height:1.3}
.feature p{font-size:10px;color:var(--muted);text-transform:uppercase;line-height:1.3}

/* about */
.about{height:560px;background:var(--soft);position:relative}
.about .portrait{position:absolute;left:120px;top:20px;width:480px;height:540px;background:radial-gradient(ellipse at 55% 45%,#cfcfcf,#9a9a9a 60%,#e8e8e8)}
.about-body{position:absolute;left:620px;top:172px;width:440px}
.about-body h2{font-size:26px;font-weight:800;color:var(--ink);margin-bottom:16px}
.about-body p{font-size:12px;margin-bottom:10px}
.about-body .btn{margin-top:18px}

/* room planner */
.planner{height:552px;position:relative}
.planner-body{position:absolute;left:132px;top:108px;width:480px}
.planner-body h2{font-size:24px;font-weight:800;color:var(--ink);padding-bottom:8px;border-bottom:2px solid var(--ink);display:inline-block;margin-bottom:18px}
.planner-body p{font-size:12px;margin-bottom:18px}
.planner-body h4{font-size:12px;font-weight:800;color:var(--ink);margin-bottom:6px}
.planner-body ul{padding-left:18px;font-size:12px;margin-bottom:22px}
.planner .plan{position:absolute;left:672px;top:92px;width:280px;height:368px;background:linear-gradient(135deg,#e6c9a2,#c9a178 50%,#a7c3d8)}

/* residential / commercial */
.services{height:416px;display:flex;position:relative}
.service{flex:1;position:relative}
.service:first-child .photo{background:linear-gradient(170deg,#8fb7d8 0%,#d5c3a6 45%,#7a5a42 100%)}
.service:last-child .photo{background:linear-gradient(170deg,#9a8a78 0%,#c07a62 50%,#4a3a32 100%)}
.service .photo{width:100%;height:100%}
.service-box{position:absolute;top:240px;width:280px;height:148px;background:var(--blue-glass);color:var(--white);padding:16px 20px}
.service:first-child .service-box{left:300px}
.service:last-child .service-box{left:120px}
.service-box h3{font-size:20px;font-weight:800;text-transform:uppercase;letter-spacing:.5px}
.service-box p{font-size:10px;line-height:1.5;margin:4px 0 10px;color:#dce7f3}

/* events */
.events{height:592px;background:var(--soft);position:relative}
.events .section-title{padding-top:60px}
.event-grid{position:absolute;top:160px;left:132px;display:flex;gap:16px}
.event{width:304px;height:364px;background:var(--white)}
.event .photo{height:192px}
.event:nth-child(1) .photo{background:linear-gradient(170deg,#9cc1df,#c9b08d 55%,#6e5641)}
.event:nth-child(2) .photo{background:linear-gradient(170deg,#5a3a2c,#a8714f 55%,#3a2820)}
.event:nth-child(3) .photo{background:linear-gradient(170deg,#4d2c24,#b0533c 55%,#2f1c18)}
.event-body{padding:14px 16px}
.event-body h3{font-size:15px;font-weight:700;color:var(--ink)}
.event-body p{font-size:10px;line-height:1.5;margin:6px 0 12px}

/* articles */
.articles{height:660px;position:relative}
.articles .section-title{padding-top:44px}
.arrow{position:absolute;width:20px;height:20px}
.articles .arrow-left{left:120px;top:352px}
.articles .arrow-right{left:1064px;top:352px}
.articles .cover{position:absolute;left:220px;top:140px;width:332px;height:400px;background:linear-gradient(160deg,#f4f2ee,#d8d3cb 40%,#8c8880)}
.article-card{position:absolute;left:540px;top:180px;width:440px;height:320px;background:var(--white);box-shadow:0 6px 26px rgba(0,0,0,.18);padding:42px 40px}
.article-card h3{font-size:18px;font-weight:700;color:var(--ink);line-height:1.35;margin-bottom:20px}
.article-card p{font-size:11px;line-height:1.55;margin-bottom:20px}

/* products */
.products{height:608px;background:var(--soft);position:relative}
.products .section-title{padding-top:56px}
.product-grid{position:absolute;top:140px;left:132px;display:flex;gap:24px}
.product{width:216px;height:324px;background:var(--white);text-align:center;padding-top:20px}
.product .photo{width:150px;height:180px;margin:0 auto;background:radial-gradient(ellipse at center,#8a5a3a 0%,#c8a487 55%,#fff 75%)}
.product:nth-child(4) .photo{background:radial-gradient(ellipse at center,#3a2a22 0%,#9a8a7e 45%,#fff 72%)}
.product h4{font-size:14px;font-weight:700;color:var(--ink);margin-top:14px}
.price{font-size:12px;margin:2px 0 10px}
.price s{color:var(--muted);margin-right:6px}
.price b{color:var(--orange)}
.products .arrow-left{left:92px;top:292px}
.products .arrow-right{left:1088px;top:292px}
.live-chat{position:absolute;right:20px;bottom:0;background:var(--orange);color:var(--white);font-weight:700;font-size:12px;text-transform:uppercase;padding:8px 18px;display:flex;gap:8px;align-items:center}
.products::after{content:"";position:absolute;left:0;right:0;bottom:0;height:4px;background:var(--orange)}

/* footer */
.site-footer{height:328px;background:var(--footer);color:#bdbdbd;position:relative}
.site-footer .brand{left:140px;top:40px;width:150px;height:96px}
.foot-col{position:absolute;top:48px;font-size:10px;line-height:1.75}
.foot-col h5{color:var(--white);font-size:11px;font-weight:700;text-transform:uppercase;margin-bottom:6px}
.foot-col.shop{left:432px}
.foot-col.company{left:592px}
.foot-col.contact{left:752px;width:130px}
.foot-col.news{left:860px}
.news-input{width:200px;height:30px;background:var(--white);color:var(--muted);font-size:10px;padding:7px 10px;margin:6px 0 10px}
.follow{position:absolute;left:140px;top:256px;display:flex;gap:10px;align-items:center;color:var(--white);font-size:11px;font-weight:700}
.follow span.dot{width:22px;height:22px;border-radius:50%;background:var(--blue)}
.copyright{position:absolute;right:132px;top:260px;font-size:10px}
.foot-rule{position:absolute;left:132px;right:132px;top:232px;border-top:1px solid #3d3d3d}
</style>
</head>
<body>

<header class="site-header">
  <div class="brand"><span class="brand-square"></span><span class="brand-name">Lori Vex Studio</span></div>
  <div class="search">
    <div class="search-cat">Category ▾</div>
    <div class="search-input">Search Products</div>
    <div class="search-go"><svg width="14" height="14" viewBox="0 0 14 14"><circle cx="6" cy="6" r="4.5" fill="none" stroke="#fff" stroke-width="2"/><line x1="9.5" y1="9.5" x2="13" y2="13" stroke="#fff" stroke-width="2"/></svg></div>
  </div>
  <div class="call">
    <div class="call-icon"><svg width="16" height="16" viewBox="0 0 16 16"><path d="M3 1.5l3 3-1.6 1.8c.9 1.8 2.3 3.2 4.3 4.3L10.5 9l3 3-2 2C6.5 13.5 2.5 9.5 1.5 3.5z" fill="#fff"/></svg></div>
    <div><small>CALL US NOW</small><strong>949-555-0148</strong></div>
  </div>
  <div class="cart"><svg width="18" height="16" viewBox="0 0 18 16"><path d="M1 1h3l2 9h9l2-6H5" fill="none" stroke="#2a2a2a" stroke-width="1.6"/><circle cx="7" cy="14" r="1.4" fill="#2a2a2a"/><circle cx="14" cy="14" r="1.4" fill="#2a2a2a"/></svg>MY CART (0)</div>
  <nav class="main-nav">
    <a href="#"><svg width="20" height="12" viewBox="0 0 20 12"><rect x="1" y="4" width="18" height="6" rx="2" fill="none" stroke="#f37122" stroke-width="1.5"/></svg>Living Room</a>
    <a href="#"><svg width="20" height="12" viewBox="0 0 20 12"><rect x="2" y="3" width="16" height="2" fill="#f37122"/><line x1="4" y1="5" x2="4" y2="12" stroke="#f37122" stroke-width="1.5"/><line x1="16" y1="5" x2="16" y2="12" stroke="#f37122" stroke-width="1.5"/></svg>Dining Room</a>
    <a href="#"><svg width="20" height="12" viewBox="0 0 20 12"><rect x="1" y="5" width="18" height="5" fill="none" stroke="#f37122" stroke-width="1.5"/><rect x="2" y="2" width="6" height="3" fill="#f37122"/></svg>Bed Room</a>
    <a href="#"><svg width="20" height="12" viewBox="0 0 20 12"><rect x="3" y="1" width="14" height="8" fill="none" stroke="#f37122" stroke-width="1.5"/><line x1="7" y1="11" x2="13" y2="11" stroke="#f37122" stroke-width="1.5"/></svg>Home Office</a>
    <a href="#"><svg width="20" height="12" viewBox="0 0 20 12"><rect x="2" y="1" width="16" height="10" rx="1" fill="none" stroke="#f37122" stroke-width="1.5"/></svg>Entertainment</a>
    <a href="#"><svg width="20" height="12" viewBox="0 0 20 12"><circle cx="10" cy="6" r="5" fill="none" stroke="#f37122" stroke-width="1.5"/></svg>Wellness</a>
    <a href="#"><svg width="20" height="12" viewBox="0 0 20 12"><path d="M10 1l3 10H7z" fill="none" stroke="#f37122" stroke-width="1.5"/></svg>Accessories</a>
    <a href="#"><svg width="20" height="12" viewBox="0 0 20 12"><path d="M4 11L14 1l2 2L6 13z" fill="#f37122"/></svg>Design Services</a>
  </nav>
</header>

<section class="hero">
  <div class="photo" role="img" aria-label="Furnished outdoor living room with white armchairs, a fireplace and warm evening lighting" style="position:absolute;inset:0;background:inherit"></div>
  <h1>Where Furniture<br>Comes to Life</h1>
  <span class="btn">Read More</span>
  <div class="dots"><span></span><span class="on"></span><span></span><span></span><span></span></div>
</section>

<section class="collections">
  <div class="cat-grid">
    <div class="cat-card"><div class="photo" role="img" aria-label="Warmly lit living room with lanterns and red accents"></div><div class="cat-label"><b>Living Room</b><span class="btn btn-sm">Shop Now</span></div></div>
    <div class="cat-card"><div class="photo" role="img" aria-label="Dining room with a wooden table and chandelier"></div><div class="cat-label"><b>Dining Room</b><span class="btn btn-sm">Shop Now</span></div></div>
    <div class="cat-card"><div class="photo" role="img" aria-label="Bedroom with a tufted headboard and neutral linens"></div><div class="cat-label"><b>Bed Room</b><span class="btn btn-sm">Shop Now</span></div></div>
  </div>
  <div class="features">
    <div class="feature"><svg width="40" height="30" viewBox="0 0 40 30"><rect x="3" y="10" width="34" height="12" rx="3" fill="none" stroke="#f37122" stroke-width="2.5"/><line x1="7" y1="22" x2="7" y2="28" stroke="#f37122" stroke-width="2.5"/><line x1="33" y1="22" x2="33" y2="28" stroke="#f37122" stroke-width="2.5"/></svg><div><h3>Design Your Own</h3><p>Customize your seating</p></div></div>
    <div class="feature"><svg width="32" height="34" viewBox="0 0 32 34"><circle cx="16" cy="13" r="10" fill="none" stroke="#f37122" stroke-width="2.5"/><rect x="11" y="25" width="10" height="6" fill="#f37122"/></svg><div><h3>Ideas &amp; Inspiration</h3><p>Decorating advice<br>from the pros</p></div></div>
    <div class="feature"><svg width="34" height="34" viewBox="0 0 34 34"><rect x="3" y="3" width="12" height="12" fill="#f37122"/><rect x="19" y="3" width="12" height="12" fill="none" stroke="#f37122" stroke-width="2.5"/><rect x="3" y="19" width="12" height="12" fill="none" stroke="#f37122" stroke-width="2.5"/><rect x="19" y="19" width="12" height="12" fill="#f37122"/></svg><div><h3>Autumn Colors</h3><p>Spice up your home<br>with harvest hues</p></div></div>
  </div>
</section>

<section class="about">
  <div class="portrait" role="img" aria-label="Black and white portrait of the designer"></div>
  <div class="about-body">
    <h2>ABOUT ME</h2>
    <p>Lori Vex Design House is a full service interior design firm led by principal designer Lori Vexmont. Every space is shaped around the way our clients live, work and gather.</p>
    <p>As a child, Lori spent countless hours in her family's workshop, learning the craft of fine furniture. That love for detail now guides each project, from custom pieces and lighting to full home installations for residential and commercial clients.</p>
    <span class="btn">Read More</span>
  </div>
</section>

<section class="planner">
  <div class="planner-body">
    <h2>ROOM PLANNER</h2>
    <p>Creating a stylish and functional room is no longer a guessing game. With our planning tool you can sketch your layout, place true to scale furniture and try colors and finishes before you buy. Save your plans, share them with friends and bring them to your next design consultation.</p>
    <h4>GET STARTED</h4>
    <ul>
      <li>Enter the room's width and length and draw its walls.</li>
      <li>Add doors and windows for a more realistic view.</li>
      <li>Position furniture and accessories to see the final look.</li>
    </ul>
    <span class="btn btn-sm">Start Planning</span>
  </div>
  <div class="plan" role="img" aria-label="Top down 3D floor plan of a furnished apartment"></div>
</section>

<section class="services">
  <div class="service"><div class="photo" role="img" aria-label="Residential patio with lounge seating overlooking the ocean"></div>
    <div class="service-box"><h3>Residential</h3><p>Custom interiors for homes that reflect how you live, from single rooms to complete renovations.</p><span class="btn btn-sm">Read More</span></div></div>
  <div class="service"><div class="photo" role="img" aria-label="Commercial restaurant interior with a long bar and red stools"></div>
    <div class="service-box"><h3>Commercial</h3><p>Hospitality, retail and office spaces designed to welcome guests and support your brand.</p><span class="btn btn-sm">Read More</span></div></div>
</section>

<section class="events">
  <h2 class="section-title">Latest Events</h2>
  <div class="event-grid">
    <div class="event"><div class="photo" role="img" aria-label="Outdoor charity gala by the water"></div><div class="event-body"><h3>House of Design 2019</h3><p>Our yearly showcase returned to the coast, bringing designers and guests together to raise funds for local families.</p><span class="btn btn-sm">Read More</span></div></div>
    <div class="event"><div class="photo" role="img" aria-label="Elegant dining setting at a benefit dinner"></div><div class="event-body"><h3>Designing For A Cause</h3><p>An evening of design and dinner where each room featured was auctioned to support children's art programs.</p><span class="btn btn-sm">Read More</span></div></div>
    <div class="event"><div class="photo" role="img" aria-label="Decorated hall prepared for a design fundraiser"></div><div class="event-body"><h3>House of Design 2013</h3><p>The first edition of our benefit house tour, where featured rooms helped fund shelters across the county.</p><span class="btn btn-sm">Read More</span></div></div>
  </div>
</section>

<section class="articles">
  <h2 class="section-title">Articles</h2>
  <svg class="arrow arrow-left" viewBox="0 0 20 20"><path d="M13 3L6 10l7 7" fill="none" stroke="#2a2a2a" stroke-width="2.5"/></svg>
  <div class="cover" role="img" aria-label="Lifestyle magazine cover featuring the studio"></div>
  <div class="article-card">
    <h3>Lorem Ipsum is simply dummy text of the printing</h3>
    <p>Lorem ipsum dolor sit amet, consectetur adipiscing elit, sed do eiusmod tempor incididunt ut labore et dolore magna aliqua. Ut enim ad minim veniam, quis nostrud exercitation ullamco laboris nisi ut aliquip ex ea commodo consequat duis aute irure.</p>
    <span class="btn btn-sm">Read More</span>
  </div>
  <svg class="arrow arrow-right" viewBox="0 0 20 20"><path d="M7 3l7 7-7 7" fill="none" stroke="#2a2a2a" stroke-width="2.5"/></svg>
</section>

<section class="products">
  <h2 class="section-title">Our Products</h2>
  <svg class="arrow arrow-left" viewBox="0 0 20 20"><path d="M13 3L6 10l7 7" fill="none" stroke="#2a2a2a" stroke-width="2.5"/></svg>
  <div class="product-grid">
    <div class="product"><div class="photo" role="img" aria-label="Upholstered armchair"></div><h4>Chairs</h4><div class="price"><s>$1200.00</s><b>$1100.00</b></div><span class="btn btn-sm">Add to Cart</span></div>
    <div class="product"><div class="photo" role="img" aria-label="Round wooden pedestal table"></div><h4>Tables</h4><div class="price"><s>$1200.00</s><b>$1100.00</b></div><span class="btn btn-sm">Add to Cart</span></div>
    <div class="product"><div class="photo" role="img" aria-label="Dark wood executive desk"></div><h4>Desks</h4><div class="price"><s>$1200.00</s><b>$1100.00</b></div><span class="btn btn-sm">Add to Cart</span></div>
    <div class="product"><div class="photo" role="img" aria-label="Tall bar stool with dark seat"></div><h4>Stools</h4><div class="price"><s>$1200.00</s><b>$1100.00</b></div><span class="btn btn-sm">Add to Cart</span></div>
  </div>
  <svg class="arrow arrow-right" viewBox="0 0 20 20"><path d="M7 3l7 7-7 7" fill="none" stroke="#2a2a2a" stroke-width="2.5"/></svg>
  <div class="live-chat"><svg width="16" height="14" viewBox="0 0 16 14"><path d="M1 1h14v9H6l-4 3v-3H1z" fill="#fff"/></svg>Live Chat</div>
</section>

<footer class="site-footer">
  <div class="brand"><span class="brand-square"></span><span class="brand-name">Lori Vex Studio</span></div>
  <div class="foot-col shop"><h5>Shop</h5>Living Room<br>Dining Room<br>Bed Room<br>Entertainment<br>Home Office<br>Wellness<br>Accessories</div>
  <div class="foot-col company"><h5>Our Company</h5>About Us<br>Concierge<br>Design Center<br>Room Planner<br>Events<br>Careers<br>Contact Us</div>
  <div class="foot-col contact"><h5>Contact Us</h5>2140 Harbor Lane<br>Harbor Vale, CA 92600<br><br>949-555-0148<br><br>info@lorivexstudio.com</div>
  <div class="foot-col news"><h5>Newsletter</h5><div class="news-input">E-mail</div><span class="btn btn-sm">Signup</span></div>
  <div class="foot-rule"></div>
  <div class="follow">FOLLOW US <span class="dot"></span><span class="dot"></span><span class="dot"></span></div>
  <div class="copyright">Copyright © 2019 Lori Vex Studio. All Rights Reserved.</div>
</footer>

</body>
</html>
```